Sales presentation introduction for Finance and Tech firms

Our business is two fold - 1) recruitment 2) consultancy. We would like a one or two page template that we can use to send to potential clients. The template will ideally be the same for the recruitment and consultancy side. We need to be able to edit the template to enter text.

I have attached our logo so you can see what we currently use on Corvella.

Sector is financial services and technology. We do not intent to have lots of text but the layout/images/designs to be used should cover some of page in a way that it takes up some space to avoid having to write lot of text.

Open to colour suggestions.

Please look at the attached word doc to see the text I would like for the two presentations.

Happy to answer questions.

Target Market(s)

Directors

Industry/Entity Type

Finance and tech companies

Colors
0094D4
00A9DD
6FCCEA
C7EBF8
E9F6FB

Requirements
Must have
• Editable text

```html
<!DOCTYPE html>
<html lang="en">
<head>
<meta charset="utf-8">
<title>Meridal Group – Consultancy and Recruitment Sheets</title>
<link href="https://fonts.googleapis.com/css2?family=Montserrat:wght@400;500;600;700;800&family=Open+Sans:wght@400;600&display=swap" rel="stylesheet">
<style>
  :root{
    --stage:#58585a;
    --paper:#ffffff;
    --blue:#1b75bb;
    --blue-deep:#0f5fa8;
    --sky:#6fcbea;
    --pale:#e6f4fb;
    --photo-light:#9fc6e6;
    --photo-mid:#3d7fbf;
    --photo-dark:#0b1f3a;
    --photo-night:#16345c;
    --ink:#222326;
    --muted:#3b3d42;
    --footer:#231f20;
    --cloud:#2a6cc0;
  }
  *{box-sizing:border-box;margin:0;padding:0}
  html,body{width:1200px;height:775px;overflow:hidden}
  body{background:var(--stage);font-family:"Montserrat",sans-serif;color:var(--ink);position:relative}

  .sheet{position:absolute;top:20px;width:520px;height:735px;background:var(--paper);overflow:hidden}
  .sheet--consultancy{left:50px}
  .sheet--recruitment{left:630px}

  .sheet__header{position:absolute;inset:0 0 auto 0;height:330px}
  .sheet__header svg{position:absolute;top:0;left:0}

  .brand{position:absolute;top:52px;left:30px;display:flex;align-items:center;gap:8px}
  .brand__dot{width:14px;height:14px;background:var(--blue)}
  .brand__name{font-weight:600;font-size:24px;letter-spacing:1.5px;color:var(--ink)}

  .tagline{position:absolute;top:110px;left:0;width:330px;height:92px;background:var(--blue);
    padding:11px 18px 0 28px;color:#fff;font-weight:700;font-size:12.5px;line-height:1.3}

  .section-title{position:absolute;left:30px;font-weight:800;font-size:13px;letter-spacing:.3px;color:var(--ink)}
  .body-copy{position:absolute;left:30px;font-size:7.3px;line-height:1.38;color:var(--muted);text-align:justify}
  .body-copy p+p{margin-top:7px}
  .body-copy strong{color:var(--blue);font-weight:700}

  /* consultancy services grid */
  .services{position:absolute;top:374px;left:28px;width:470px;display:grid;grid-template-columns:repeat(3,1fr);row-gap:4px}
  .service{display:flex;align-items:center;gap:10px;height:42px}
  .service__badge{flex:none;width:40px;height:40px;border-radius:50%;background:var(--blue);position:relative}
  .service__badge::after{content:"";position:absolute;inset:4px;border:1.5px solid #fff;border-radius:50%}
  .service__label{font-size:9px;font-weight:500;line-height:1.2;color:var(--ink)}

  .capabilities{position:absolute;top:518px;left:0;width:520px;height:172px;background:var(--pale)}
  .capability{position:absolute;width:236px;display:flex;gap:10px}
  .capability__icon{flex:none;width:36px;height:36px;border:2px solid var(--blue);border-radius:8px;margin-top:4px;position:relative}
  .capability__icon::after{content:"";position:absolute;inset:8px;border:2px solid var(--blue);border-radius:50%}
  .capability h3{font-size:11px;font-weight:700;color:var(--blue-deep);margin-bottom:2px}
  .capability p{font-size:6.6px;line-height:1.32;color:var(--muted);text-align:justify}

  /* recruitment */
  .checklist{list-style:none;font-size:7.3px;line-height:1.9;color:var(--muted)}
  .checklist li{display:flex;align-items:center;gap:6px}
  .checklist li::before{content:"";width:6px;height:6px;border-radius:50%;background:var(--blue);flex:none}
  .checklist--wide{display:grid;grid-template-columns:1fr 1fr;column-gap:12px;row-gap:8px;line-height:1.3}
  .checklist--wide li{align-items:flex-start;text-align:left}
  .checklist--wide li::before{margin-top:2px}

  .skills{position:absolute;top:540px;left:0;width:520px;height:150px;background:var(--pale);font-family:"Open Sans",sans-serif;color:var(--cloud)}
  .skills span{position:absolute;white-space:nowrap}

  .sheet__footer{position:absolute;left:0;bottom:0;width:520px;height:45px;background:var(--footer);color:#fff;
    display:flex;align-items:center;justify-content:space-around;font-size:10px;font-weight:600}
  .contact{display:flex;align-items:center;gap:6px}
  .contact svg{flex:none}
</style>
</head>
<body>

<!-- Consultancy sheet -->
<section class="sheet sheet--consultancy">
  <div class="sheet__header">
    <svg width="520" height="330" viewBox="0 0 520 330">
      <defs>
        <linearGradient id="skyline" x1="0" y1="0" x2="1" y2="1">
          <stop offset="0" stop-color="var(--photo-light)"/>
          <stop offset=".55" stop-color="var(--photo-mid)"/>
          <stop offset="1" stop-color="#1d4f8a"/>
        </linearGradient>
      </defs>
      <polygon points="150,0 520,0 520,150 385,300" fill="url(#skyline)" role="img" aria-label="Photo looking up at glass office towers against a blue sky"/>
      <polygon points="385,300 520,150 520,178 398,318" fill="var(--blue-deep)"/>
      <polygon points="372,300 385,300 398,318 383,318" fill="var(--blue)"/>
      <polygon points="420,315 520,205 520,315" fill="var(--sky)"/>
      <polygon points="440,315 520,228 520,235 447,315" fill="#fff"/>
    </svg>
    <div class="brand"><span class="brand__dot"></span><span class="brand__name">MERIDAL GROUP</span></div>
    <div class="tagline">A partner who brings new and innovative ideas to the table, through extensive industry experience and knowledge. Meridal will ensure you are prepared for growth.</div>
  </div>

  <h2 class="section-title" style="top:232px">MERIDAL CONSULTANCY</h2>
  <div class="body-copy" style="top:252px;width:298px">
    <p>Meridal Group is a bespoke consultancy firm that specialises in buy side investment. Through an industry based consultative approach we assist our clients in preparing for, and facilitating, long term growth. Working closely with our clients we combine innovative thinking and breakthrough technologies to accelerate progress and, together, achieve enduring results.</p>
    <p>Experienced in successfully delivering change for global organisations as well as assisting smaller firms during their growth phase. Meridal will work with you to create a workable model and ensure successful delivery of the project.</p>
  </div>

  <div class="services">
    <div class="service"><span class="service__badge"></span><span class="service__label">Order<br>Management<br>and Trading</span></div>
    <div class="service"><span class="service__badge"></span><span class="service__label">CRM/ Onboarding</span></div>
    <div class="service"><span class="service__badge"></span><span class="service__label">Compliance</span></div>
    <div class="service"><span class="service__badge"></span><span class="service__label">Investment<br>and<br>Research</span></div>
    <div class="service"><span class="service__badge"></span><span class="service__label">Performance,<br>Risk and<br>Attribution</span></div>
    <div class="service"><span class="service__badge"></span><span class="service__label">Finance<br>and<br>Accounting</span></div>
    <div class="service"><span class="service__badge"></span><span class="service__label">Investment<br>and<br>Research</span></div>
    <div class="service"><span class="service__badge"></span><span class="service__label">Client and<br>Regulatory<br>Reporting</span></div>
    <div class="service"><span class="service__badge"></span><span class="service__label">Middle<br>and<br>Back Office</span></div>
  </div>

  <div class="capabilities">
    <article class="capability" style="top:12px;left:24px">
      <span class="capability__icon"></span>
      <div><h3>Business Strategy</h3><p>Meridal will help you create a business strategy tailored to your requirements. Ensuring each business process is defined and taken into account allows for a successful design. Creating and implementing an operating model that takes into account budget, resources, culture and your company's vision.</p></div>
    </article>
    <article class="capability" style="top:4px;left:266px">
      <span class="capability__icon"></span>
      <div><h3>Change management</h3><p>Meridal works with clients to deliver bespoke change initiatives. Rigorous business analysis and risk management allows for successful change initiatives. We work with you throughout the complete process, to ensure that delivery is based on value. Transition phases are challenging aspects of change which is why our team manage all transitions and the risk they carry.</p></div>
    </article>
    <article class="capability" style="top:94px;left:24px">
      <span class="capability__icon"></span>
      <div><h3>IT transformation</h3><p>Meridal is widely experienced in a range of technologies. We help with the implementation of software provider or design and develop bespoke services. Covering front to back office the team specialises in full project lifecycle from feasibility through to implementation.</p></div>
    </article>
    <article class="capability" style="top:100px;left:266px">
      <span class="capability__icon"></span>
      <div><h3>Organisational structure</h3><p>Meridal works with clients to improve resource capability and strategic partnerships. Acting as an extension of the HR function, we analyse business processes and ensure that our clients have the ability to manage changing workforce demands.</p></div>
    </article>
  </div>

  <footer class="sheet__footer">
    <span class="contact"><svg width="14" height="14" viewBox="0 0 14 14"><circle cx="7" cy="7" r="6.2" fill="none" stroke="#fff"/><path d="M4.6 4.2l1.3-.4.7 1.6-.8.6c.4.9 1 1.5 1.9 1.9l.6-.8 1.6.7-.4 1.3c-2.6 0-4.9-2.3-4.9-4.9z" fill="#fff"/></svg>+44 (0) 7700 900412</span>
    <span class="contact"><svg width="14" height="14" viewBox="0 0 14 14"><circle cx="7" cy="7" r="6.2" fill="none" stroke="#fff"/><rect x="3.8" y="4.8" width="6.4" height="4.4" fill="none" stroke="#fff" stroke-width=".9"/><path d="M3.8 4.8L7 7.3l3.2-2.5" fill="none" stroke="#fff" stroke-width=".9"/></svg>hello@meridalgroup.com</span>
    <span class="contact"><svg width="14" height="14" viewBox="0 0 14 14"><circle cx="7" cy="7" r="6.2" fill="none" stroke="#fff"/><circle cx="7" cy="7" r="3.4" fill="none" stroke="#fff" stroke-width=".9"/><path d="M3.6 7h6.8M7 3.6v6.8" stroke="#fff" stroke-width=".8"/></svg>www.meridalgroup.com</span>
  </footer>
</section>

<!-- Recruitment sheet -->
<section class="sheet sheet--recruitment">
  <div class="sheet__header">
    <svg width="520" height="330" viewBox="0 0 520 330">
      <defs>
        <radialGradient id="network" cx=".65" cy=".45" r=".7">
          <stop offset="0" stop-color="#5d8fc4"/>
          <stop offset=".4" stop-color="var(--photo-night)"/>
          <stop offset="1" stop-color="var(--photo-dark)"/>
        </radialGradient>
      </defs>
      <polygon points="150,0 520,0 520,150 385,300" fill="url(#network)" role="img" aria-label="Photo of a hand touching a glowing digital network of finance icons"/>
      <polygon points="385,300 520,150 520,178 398,318" fill="var(--blue-deep)"/>
      <polygon points="372,300 385,300 398,318 383,318" fill="var(--blue)"/>
      <polygon points="420,315 520,205 520,315" fill="var(--sky)"/>
      <polygon points="440,315 520,228 520,235 447,315" fill="#fff"/>
    </svg>
    <div class="brand"><span class="brand__dot"></span><span class="brand__name">MERIDAL GROUP</span></div>
    <div class="tagline">A partner who brings new and innovative ideas to the table, through extensive industry experience and knowledge. Meridal will ensure you are prepared for growth.</div>
  </div>

  <h2 class="section-title" style="top:222px">MERIDAL RECRUITMENT</h2>
  <div class="body-copy" style="top:242px;width:292px">
    <p>Meridal is more than an ordinary recruitment service. Our experts work with clients to develop a HR strategy that maps current, and impending, organisational needs; using research to effectively benchmark. We are developing various talent communities that provide effective, and timely, recruitment solutions for our clients.</p>
    <p><strong>SPECIALISTS IN:</strong> Asset Management recruitment with a specialisation in I.T, Operations, Regulation and Change Management.</p>
  </div>

  <div class="body-copy" style="top:346px;width:200px">
    <p>Meridal acts as an extension of your HR function, providing an end-to-end permanent and contingent talent acquisition solution, taking full accountability and ownership for the entire recruitment process, which includes:</p>
    <ul class="checklist" style="margin-top:6px">
      <li>Workforce Planning</li>
      <li>Strategic Sourcing</li>
      <li>Talent Engagement</li>
      <li>Candidate Management</li>
      <li>Weekly vacancy updates</li>
    </ul>
  </div>

  <div class="body-copy" style="top:346px;left:250px;width:240px">
    <p>We recognise that hiring can be a lengthy process, therefore we partner with you to ensure you only interview top quantile candidates, cutting out multiple meetings with multiple candidates. Giving hiring managers time back in their diaries to do their day jobs and reducing the time to hire. This is achieved by:</p>
    <ul class="checklist checklist--wide" style="margin-top:6px">
      <li>Understanding the roles, and partnering with you to build meaningful job descriptions</li>
      <li>Support with interviews and we ensure the candidate has a positive experience</li>
      <li>Candidates are fully screened and interviewed prior to presentation to you</li>
      <li>Qualified shortlist of top 3 candidates</li>
    </ul>
  </div>

  <div class="body-copy" style="top:496px;width:460px">
    <p>Meridal recruitment partners with principal business consultants from Meridal consultancy to ensure candidates are properly screened before presenting to our clients. This allows for our clients to focus on only interviewing the best on the market.</p>
  </div>

  <div class="skills">
    <span style="top:18px;left:40px;font-size:20px">Fixed Income</span>
    <span style="top:22px;left:215px;font-size:15px">Trading Platforms</span>
    <span style="top:16px;left:355px;font-size:14px">MIS</span>
    <span style="top:6px;left:392px;font-size:17px">Cloud Stack</span>
    <span style="top:30px;left:398px;font-size:7px">Settlement</span>
    <span style="top:54px;left:30px;font-size:14px">Equity</span>
    <span style="top:44px;left:100px;font-size:28px">SQL</span>
    <span style="top:48px;left:160px;font-size:7.5px">Data Lake</span>
    <span style="top:46px;left:236px;font-size:17px">Workflow Management</span>
    <span style="top:38px;left:432px;font-size:14px">FIX/Swift</span>
    <span style="top:70px;left:380px;font-size:7px">Collateral Management</span>
    <span style="top:80px;left:370px;font-size:19px">Connectivity</span>
    <span style="top:98px;left:35px;font-size:15px">Business Intelligence</span>
    <span style="top:92px;left:205px;font-size:10px">XML</span>
    <span style="top:94px;left:248px;font-size:10px">Pricing and analytics</span>
    <span style="top:108px;left:205px;font-size:20px">Reference data</span>
    <span style="top:108px;left:376px;font-size:14px">Batch processing</span>
    <span style="top:124px;left:30px;font-size:15px">Risk and attribution</span>
  </div>

  <footer class="sheet__footer">
    <span class="contact"><svg width="14" height="14" viewBox="0 0 14 14"><circle cx="7" cy="7" r="6.2" fill="none" stroke="#fff"/><path d="M4.6 4.2l1.3-.4.7 1.6-.8.6c.4.9 1 1.5 1.9 1.9l.6-.8 1.6.7-.4 1.3c-2.6 0-4.9-2.3-4.9-4.9z" fill="#fff"/></svg>+44 (0) 7700 900412</span>
    <span class="contact"><svg width="14" height="14" viewBox="0 0 14 14"><circle cx="7" cy="7" r="6.2" fill="none" stroke="#fff"/><rect x="3.8" y="4.8" width="6.4" height="4.4" fill="none" stroke="#fff" stroke-width=".9"/><path d="M3.8 4.8L7 7.3l3.2-2.5" fill="none" stroke="#fff" stroke-width=".9"/></svg>hello@meridalgroup.com</span>
    <span class="contact"><svg width="14" height="14" viewBox="0 0 14 14"><circle cx="7" cy="7" r="6.2" fill="none" stroke="#fff"/><circle cx="7" cy="7" r="3.4" fill="none" stroke="#fff" stroke-width=".9"/><path d="M3.6 7h6.8M7 3.6v6.8" stroke="#fff" stroke-width=".8"/></svg>www.meridalgroup.com</span>
  </footer>
</section>

</body>
</html>
```